Biscuits by Marnie Labels for a cookie jar

The website you can draw from is www.biscuitsbyMarnie.example in particular we are making a product brand label, the only change will be the name of the cookie we are promoting. We are providing you with two examples that we are using 1)coconut chocolate chip cookie bite 2) cranberry oatmeal cookie bite, in two sizes a 200g and a 500g bucket, the dementions are 4 1/4 " diameter x 4 1/2" height, our slogan that needs to be on the label is: A Crock of Crumbs. Attached is a picture of the container we need the labels for.

For the back label it should have the Nutritional facts, the barcodes, the ingredients, our website, blank spot for the best before date. Manufacturing Biscuits by Marnie in Fernvale, BC as well as the 1-866-555-0147.

Please put the caption on the back as follows: Family traditions the old fashion way with whole foods and ancient grains passed down from generations within my Danish family.

Coconut Chocolate Chip Cookie Ingredients: Organic Flour, Dark Chocolate Chips, Organic Cane Sugar, Organic Cane Brown Sugar, Organic Butter, Coconut Oil, Organic Eggs, Pure Vanilla, Organic Baking Soda, Kosher Salt

Cranberry Oatmeal Cookie: Gluten Free Rolled Oats, Organic Flour, Organic Butter, Organic Cane Sugar,Cranberries, Organic Cane Brown Sugar, Organic Eggs, Organic Coconut, Chia Seeds, Pure Vanilla,Kosher Salt,Spices,

Target Market(s)

This cookie ia all organic so a person who is health minded

Industry/Entity Type

Grocery Store

Requirements
Must have
• - For the back label it should have the Nutritional facts, the barcodes, the ingredients, our website, blank spot for the best before date. Manufacturing Biscuits by Marnie in Fernvale, BC as well as the 1-866-555-0147.
• - Biscuits by Marnie on the front label
• - our slogan that needs to be on the label is: A Crock of Crumbs.
• - Nutritional facts

```html
<!DOCTYPE html>
<html lang="en">
<head>
<meta charset="utf-8">
<title>A Crock of Crumbs – Jar Labels</title>
<link rel="stylesheet" href="https://fonts.googleapis.com/css2?family=Kurale&family=Ubuntu:wght@500&family=Open+Sans:wght@400;700&family=Marcellus+SC&family=Arimo:wght@400;700&family=Libre+Franklin:wght@900&display=swap">
<style>
  :root {
    --backdrop: #c9c6c1;
    --cream: #f5ebdf;
    --cream-deep: #efe0cf;
    --caramel: #9a4812;
    --toffee: #d9a266;
    --toffee-light: #e9cba6;
    --cocoa: #3e2c24;
    --ink: #3a2a22;
    --black: #111111;
    --white: #ffffff;
  }
  html, body { margin: 0; padding: 0; overflow: hidden; background: var(--backdrop); }
  .canvas { position: relative; width: 1200px; height: 654px; overflow: hidden; background: var(--backdrop); }

  .label { position: absolute; border-radius: 50%; overflow: hidden; }
  .label svg { position: absolute; inset: 0; }

  /* Front label */
  .label--front { left: 16px; top: 56px; width: 568px; height: 568px; }
  .product-name {
    position: absolute; left: 24px; width: 544px; top: 162px; margin: 0; text-align: center;
    font-family: "Ubuntu", sans-serif; font-weight: 500; font-size: 44px; line-height: 52px; color: var(--ink);
  }
  .flavour {
    position: absolute; left: 24px; width: 544px; top: 220px; margin: 0; text-align: center;
    font-family: "Ubuntu", sans-serif; font-weight: 500; font-size: 22px; line-height: 28px; color: var(--ink);
  }
  .net-weight {
    position: absolute; left: 452px; top: 294px;
    font-family: "Kurale", serif; font-size: 19px; line-height: 24px; color: var(--ink);
  }
  .bakery-name {
    position: absolute; left: 108px; width: 400px; top: 496px; text-align: center;
    font-family: "Open Sans", sans-serif; font-weight: 700; font-size: 20px; line-height: 26px; color: var(--white);
  }

  /* Back label */
  .label--back { left: 655px; top: 55px; width: 571px; height: 571px; }
  .story {
    position: absolute; left: 80px; width: 410px; top: 92px; margin: 0; text-align: center;
    font-family: "Open Sans", sans-serif; font-size: 15px; line-height: 19.2px; color: var(--black); text-transform: uppercase;
  }
  .ingredients-title {
    position: absolute; left: 63px; top: 218px; margin: 0;
    font-family: "Open Sans", sans-serif; font-weight: 400; font-size: 17.5px; line-height: 24px; color: var(--black);
  }
  .ingredients-list {
    position: absolute; left: 61px; top: 255px; width: 250px; margin: 0;
    font-family: "Open Sans", sans-serif; font-size: 14px; line-height: 17px; letter-spacing: 0.3px; color: var(--black);
  }
  .best-before {
    position: absolute; left: 62px; top: 396px; margin: 0;
    font-family: "Open Sans", sans-serif; font-size: 14px; line-height: 18px; letter-spacing: 0.6px; color: var(--black);
  }
  .maker {
    position: absolute; left: 70px; width: 410px; top: 460px; margin: 0; text-align: center;
    font-family: "Marcellus SC", serif; font-size: 14.5px; line-height: 18px; color: var(--black); letter-spacing: 0.5px;
  }
  .website {
    position: absolute; left: 250px; top: 484px; margin: 0;
    font-family: "Marcellus SC", serif; font-size: 14px; line-height: 18px; color: var(--black); letter-spacing: 0.5px;
  }
  .phone {
    position: absolute; left: 291px; top: 508px; margin: 0;
    font-family: "Open Sans", sans-serif; font-size: 14.5px; line-height: 18px; color: var(--black); letter-spacing: 1.5px;
  }

  /* Nutrition panel */
  .nutrition {
    position: absolute; left: 316px; top: 198px; width: 187px; height: 255px; box-sizing: border-box;
    background: var(--white); border: 3px solid var(--toffee); padding: 3px 6px;
    font-family: "Arimo", sans-serif; font-size: 7px; line-height: 10px; color: var(--black);
  }
  .nutrition__title { margin: 0; font-family: "Libre Franklin", sans-serif; font-weight: 900; font-size: 18px; line-height: 19px; }
  .nutrition__row { display: flex; justify-content: space-between; border-top: 0.6px solid var(--black); }
  .nutrition__row--indent { padding-left: 9px; }
  .nutrition__rule-thick { height: 5px; background: var(--black); margin: 1px 0; }
  .nutrition__rule-mid { height: 2px; background: var(--black); }
  .nutrition__plain { border-top: none; }
  .nutrition b { font-weight: 700; }
  .nutrition__note { font-size: 5.6px; line-height: 6.4px; margin: 1px 0 2px; border-top: 0.6px solid var(--black); padding-top: 1px; }
  .nutrition__source { border: 0.8px solid var(--black); text-align: center; font-weight: 700; font-size: 6.5px; background: #f1f1f1; }
</style>
</head>
<body>
<main class="canvas">

  <section class="label label--front" aria-label="Front label">
    <svg width="568" height="568" viewBox="0 0 568 568">
      <rect width="568" height="568" fill="var(--cream)"/>
      <path d="M0 382 C160 366 400 340 568 255 L568 568 L0 568Z" fill="var(--caramel)"/>
      <path d="M0 398 C170 386 410 372 568 300 L568 568 L0 568Z" fill="var(--toffee)"/>
      <path d="M0 556 C190 536 390 566 568 540 L568 568 L0 568Z" fill="var(--cream)"/>
      <circle cx="380" cy="388" r="100" fill="var(--cream)"/>
      <circle cx="380" cy="388" r="89" fill="var(--cocoa)"/>
      <ellipse cx="380" cy="392" rx="76" ry="42" fill="#c28a52" role="img" aria-label="Photo of three chocolate chip cookies"/>
    </svg>
    <h1 class="product-name">A Crock of Crumbs</h1>
    <p class="flavour">coconut chocolate chip cookies</p>
    <span class="net-weight">200g</span>
    <span class="bakery-name">Biscuits by Marnie BAKERY</span>
  </section>

  <section class="label label--back" aria-label="Back label">
    <svg width="571" height="571" viewBox="0 0 571 571">
      <defs>
        <linearGradient id="bakingScene" x1="0" y1="0" x2="0" y2="1">
          <stop offset="0" stop-color="#dcc6ad"/>
          <stop offset="0.55" stop-color="#f2e6d8"/>
          <stop offset="1" stop-color="var(--cream)"/>
        </linearGradient>
      </defs>
      <rect width="571" height="571" fill="var(--cream)"/>
      <rect width="571" height="400" fill="url(#bakingScene)" role="img" aria-label="Photo of bowls of flour, eggs and a whisk on a baking table"/>
      <path d="M0 377 C180 350 400 380 571 313 L571 571 L0 571Z" fill="var(--toffee-light)"/>
      <path d="M0 470 C200 440 400 470 571 430 L571 571 L0 571Z" fill="var(--cream-deep)"/>
    </svg>
    <p class="story">Family traditions the old fashion way<br>with whole foods and ancient grains<br>passed down from generations within my<br>Danish family</p>
    <h2 class="ingredients-title">Ingredients:</h2>
    <p class="ingredients-list">Organic Flour, Dark Chocolate<br>Chips, Organic Cane Sugar,<br>Organic Cane Brown Sugar,<br>Organic Butter, Coconut Oil,<br>Organic Eggs, Pure Vanilla,<br>Organic Baking Soda, Kosher<br>Salt</p>
    <p class="best-before">BEST BEFORE DATE</p>

    <div class="nutrition" aria-label="Nutrition Facts">
      <p class="nutrition__title">Nutrition Facts</p>
      <div class="nutrition__row nutrition__plain">Serving Size 1 cup, chopped (125g)</div>
      <div class="nutrition__rule-thick"></div>
      <div class="nutrition__row nutrition__plain"><b style="font-size:5.8px">Amount Per Serving</b></div>
      <div class="nutrition__row"><span><b>Calories</b> 773</span><span>Calories from Fat 617</span></div>
      <div class="nutrition__rule-mid"></div>
      <div class="nutrition__row nutrition__plain" style="justify-content:flex-end"><b>% Daily Value*</b></div>
      <div class="nutrition__row"><span><b>Total Fat</b> 74g</span><span>113%</span></div>
      <div class="nutrition__row nutrition__row--indent"><span>Saturated Fat 4g</span><span>21%</span></div>
      <div class="nutrition__row nutrition__row--indent"><span>Trans Fat</span><span></span></div>
      <div class="nutrition__row"><span><b>Cholesterol</b> 0mg</span><span>0%</span></div>
      <div class="nutrition__row"><span><b>Sodium</b> 2mg</span><span>0%</span></div>
      <div class="nutrition__row"><span><b>Total Carbohydrate</b> 12g</span><span>4%</span></div>
      <div class="nutrition__row nutrition__row--indent"><span>Dietary Fiber 8g</span><span>34%</span></div>
      <div class="nutrition__row nutrition__row--indent"><span>Sugars 1g</span><span></span></div>
      <div class="nutrition__row"><span><b>Protein</b> 30g</span><span></span></div>
      <div class="nutrition__rule-thick"></div>
      <div class="nutrition__row nutrition__plain"><span>Vitamin A &nbsp;&nbsp;&nbsp;&nbsp;1% &nbsp;•&nbsp; Vitamin C</span><span>4%</span></div>
      <div class="nutrition__row"><span>Calcium &nbsp;&nbsp;&nbsp;&nbsp;&nbsp;&nbsp;&nbsp;8% &nbsp;•&nbsp; Iron</span><span>22%</span></div>
      <p class="nutrition__note">*Percent Daily Values are based on a 2,000 calorie diet. Your daily values may be higher or lower depending on your calorie needs.</p>
      <div class="nutrition__source">NutriFacts.example</div>
    </div>

    <p class="maker">Manufacturing Biscuits by Marnie in Fernvale, BC</p>
    <p class="website">www.biscuitsbyMarnie.example</p>
    <p class="phone">1-866-555-0147</p>
  </section>

</main>
</body>
</html>
```